Poster design for - Silver Heron Gathering

To design a dynamic illustrated Silver Heron Gathering poster.
The dates are: 3-5 July 2020
Location: Fennick Meadow, Tarwick, Bedfordshire
www.silverheronmeet.co.uk

Here is some text about the event to give you an idea. You can take elements from it if you like:

A Gathering of Female Energy to Ignite and Embrace the Power of Woman with Mother Earth.

Target Market(s)

Women festival goers.

Industry/Entity Type

Festival

Colors

Designer to choose colors to be used in the design.

Requirements
Must have
• Silver Heron Logo - but this can be altered to look washed out.
• Date, location, website url.
Nice to have
• Earthy, hippy, festival look.

```html
<!DOCTYPE html>
<html lang="en">
<head>
<meta charset="utf-8">
<title>Silver Heron Gathering – 3-5 July 2020</title>
<link rel="stylesheet" href="https://fonts.googleapis.com/css2?family=Nunito:wght@800;900&family=Open+Sans:wght@600&family=Courgette&family=Didact+Gothic&display=swap">
<style>
  :root {
    --flame-red: #e8321e;
    --ink: #1c1c1c;
    --body-ink: #3a3a3a;
    --brand-grey: #3d4448;
    --paper-light: #fdf0e2;
    --paper-peach: #f9cf9f;
    --paper-orange: #f5a45e;
    --paper-coral: #f08060;
  }
  html, body { margin: 0; padding: 0; overflow: hidden; }
  body { background: #ffffff; }
  .poster {
    position: relative;
    width: 848px;
    height: 1200px;
    overflow: hidden;
    color: var(--ink);
  }
  .watercolour-wash {
    position: absolute;
    inset: 0;
    background:
      radial-gradient(ellipse at 85% 90%, var(--paper-coral) 0%, transparent 45%),
      radial-gradient(ellipse at 95% 20%, var(--paper-orange) 0%, transparent 40%),
      radial-gradient(ellipse at 10% 95%, var(--paper-peach) 0%, transparent 45%),
      linear-gradient(160deg, var(--paper-light) 0%, #fbe0c0 40%, var(--paper-peach) 70%, var(--paper-orange) 100%);
  }
  .brand {
    position: absolute;
    left: 68px;
    top: 120px;
    width: 334px;
    display: flex;
    align-items: center;
    justify-content: center;
    gap: 14px;
  }
  .brand-dot {
    width: 34px;
    height: 34px;
    border-radius: 50%;
    background: var(--brand-grey);
    flex: none;
  }
  .brand-name {
    font-family: "Nunito", sans-serif;
    font-weight: 800;
    font-size: 34px;
    line-height: 1.1;
    color: var(--brand-grey);
  }
  .event-details {
    position: absolute;
    right: 27px;
    top: 148px;
    text-align: right;
    font-family: "Nunito", sans-serif;
    font-weight: 900;
    text-shadow: 1px 1px 0 rgba(0,0,0,0.35);
  }
  .event-date { font-size: 36px; line-height: 44px; }
  .event-place { font-size: 17px; line-height: 29px; font-weight: 800; margin-top: 4px; }
  .tagline {
    position: absolute;
    left: 0;
    right: 0;
    top: 296px;
    margin: 0;
    text-align: center;
    padding-left: 20px;
    font-family: "Open Sans", sans-serif;
    font-weight: 600;
    font-size: 13.5px;
    line-height: 24px;
    color: var(--flame-red);
  }
  .welcome {
    position: absolute;
    left: 0;
    right: 0;
    top: 366px;
    margin: 0;
    text-align: center;
    font-family: "Courgette", cursive;
    font-weight: 400;
    font-size: 42px;
    color: var(--flame-red);
    text-shadow: 2px 2px 0 var(--ink);
  }
  .join-list {
    position: absolute;
    right: 27px;
    top: 468px;
    width: 760px;
    text-align: right;
    font-family: "Nunito", sans-serif;
    font-weight: 800;
    font-size: 14px;
    line-height: 24.3px;
    text-shadow: 1px 1px 0 rgba(0,0,0,0.25);
  }
  .join-list p { margin: 0; }
  .join-us {
    font-family: "Open Sans", sans-serif;
    font-weight: 600;
    font-size: 18.5px;
    color: var(--flame-red);
    text-shadow: none;
  }
  .about {
    position: absolute;
    left: 30px;
    top: 668px;
    width: 700px;
    font-family: "Didact Gothic", sans-serif;
    font-size: 12.3px;
    line-height: 21.4px;
    color: var(--body-ink);
  }
  .about p { margin: 0; }
  .about .lead { font-size: 15px; }
  .about h2 {
    margin: 0;
    font-family: "Didact Gothic", sans-serif;
    font-weight: 400;
    font-size: 16px;
    line-height: 21px;
    color: var(--body-ink);
  }
  .website {
    position: absolute;
    left: 0;
    right: 0;
    top: 1134px;
    text-align: center;
    font-family: "Nunito", sans-serif;
    font-weight: 900;
    font-size: 25px;
    text-shadow: 1px 1px 0 rgba(0,0,0,0.3);
  }
</style>
</head>
<body>
<main class="poster">
  <div class="watercolour-wash" role="img" aria-label="Soft orange and peach watercolour paint texture background"></div>

  <div class="brand">
    <div class="brand-dot"></div>
    <div class="brand-name">Silver Heron</div>
  </div>

  <div class="event-details">
    <div class="event-date">3-5 July 2020</div>
    <div class="event-place">Location: Fennick Meadow,<br>Tarwick, Bedfordshire</div>
  </div>

  <p class="tagline">A Gathering of Female Energy to Ignite and Embrace<br>the Power of Woman with Mother Earth</p>

  <h1 class="welcome">Silver Heron - welcome!</h1>

  <div class="join-list">
    <p><span class="join-us">Join us</span> - in the heart of the fire!</p>
    <p><span class="join-us">Join us</span> - a gathering of incredible women from across this beautiful planet.</p>
    <p><span class="join-us">Join us</span> - in our heart-space of laughter, knowledge, fun, creativity, friendship, healing,<br>growth and wildness, immersed in nature.</p>
    <p><span class="join-us">Join us</span> for the weekend of July 3rd- 5th 2020 for the 1st Silver Heron Gathering in the beautiful<br>setting of Tarwick in Bedfordshire.</p>
  </div>

  <section class="about">
    <p><span class="lead">Silver Heron</span> is just for one weekend but its impact will last a lifetime.</p>
    <p>The whole two days will be you-time.</p>
    <p>Time for you to relish new experiences, develop new skills and make new friends simply attending,</p>
    <p>you will be honouring your own feminine power and paying homage to womanhood.</p>
    <p>Your presence will add immeasurably to the experience of your fellow attendees.</p>
    <p>Fill your heart and soul with a weekend of enlightened talks, workshops and classes,</p>
    <p>followed by an evening filled with music, dance, fire performers, fire walking, campfire,</p>
    <p>marshmallow toasting, stories and igniting the Silver Heron!</p>
    <h2>Who is Silver Heron?</h2>
    <p>Silver Heron has a fire burning within. Silver Heron is ready to let her flames burn higher and</p>
    <p>shine brighter. Silver Herons together are stronger, brighter and wilder still.</p>
    <p>Creativity and courage fires us and inspires us. We carry a torch for ourselves and for every woman –</p>
    <p>the torch of purpose, passion and power.A festival only for women?</p>
    <p>This is a festival run by women for women … and here’s why –</p>
    <p>The Silver Heron <span class="lead">festival</span> is a beautiful heart-space for women to relax, rejuvenate, celebrate,</p>
    <p>connect, flourish, transform and take time for themselves. Throughout history, <span class="lead">women</span> have shared</p>
    <p>common experiences of cultural conditioning.</p>
    <p>These experiences have impacted harshly on our confidence and identity. Ignite your soul.</p>
    <p><span class="lead">The power</span> of the Silver Heron experience is a power that ignites souls, radiates warmth and shares light.</p>
    <p>Renewed and regenerated, your empowerment will spread to others.Touch the power and you will be inspired.</p>
    <p>Touch others and you, in turn, will <span class="lead">inspire</span> them.</p>
  </section>

  <div class="website">www.silverheronmeet.co.uk</div>
</main>
</body>
</html>
```